Quillmere Supply Chain and Logistic Consulting

Please review the attached Business Card. I want as close to this card with the colors, fonts, and quality of the card as possible. The attached compass should replace the deer head on both sides of the card and the text should say:

Backside
Compass JPEG
Quillmere Logistics
A Supply Chain and Logistics Consulting Company

Frontside
Quillmere Logistics
Ray Falkner - Harlow Bay Coast
President
____________________________________
(555) 314-9027
QuillmereSCL@Examplemail.com
_____________________________________

Bottom Front Side

Target Market(s)

Businesses

Contact Information for Business Card

Backside
Compass JPEG
Quillmere Logistics

Frontside
Quillmere Logistics
President
(555) 314-9027
QuillmereSCL@Examplemail.com

Bottom Front Side

Font styles to use
Serif
Script

Colors

Designer to choose colors to be used in the design.

Requirements
Must have
• See attached card for reference
Nice to have
Should not have

```html
<!DOCTYPE html>
<html lang="en">
<head>
<meta charset="utf-8">
<title>Quillmere Logistics Business Card</title>
<link rel="stylesheet" href="https://fonts.googleapis.com/css2?family=Tinos:wght@400;700&display=swap">
<style>
  :root {
    --backdrop: #2e2926;
    --card: #0e0e0f;
    --card-edge: #1c1c1e;
    --ink: #f2f2f2;
    --ink-soft: #c9c9cc;
    --silver: #b9bcc2;
    --rule: #3e3e42;
    --steel-blue: #4a6a9c;
  }
  * { margin: 0; padding: 0; box-sizing: border-box; }
  html, body {
    width: 1200px; height: 844px; overflow: hidden;
    background: var(--backdrop);
    font-family: "Tinos", "Times New Roman", serif;
  }
  .stage {
    position: relative; width: 1200px; height: 844px;
    display: flex; align-items: center; justify-content: center; gap: 60px;
  }
  .card {
    position: relative; width: 520px; height: 297px;
    background: var(--card);
    border: 1px solid var(--card-edge);
    color: var(--ink);
  }
  /* Front */
  .brand-mark {
    position: absolute; left: 40px; top: 40px; width: 170px;
    display: flex; flex-direction: column; align-items: center; gap: 10px;
  }
  .brand-mark__circle {
    width: 110px; height: 110px; border-radius: 50%;
    background: radial-gradient(circle, #3d5a88 0%, #22324d 70%, #141a24 100%);
  }
  .brand-mark__name {
    font-size: 15px; color: var(--steel-blue); letter-spacing: 1px;
  }
  .divider {
    position: absolute; left: 238px; top: 28px; width: 1px; height: 175px;
    background: var(--rule);
  }
  .contact { position: absolute; left: 258px; top: 34px; }
  .contact__name, .contact__city {
    font-weight: 700; font-size: 18px; line-height: 21px;
  }
  .contact__title {
    font-weight: 700; font-size: 13px; margin-top: 2px;
  }
  .contact__list { list-style: none; margin-top: 12px; }
  .contact__item {
    display: flex; align-items: center; gap: 6px;
    font-size: 14px; line-height: 20px; color: var(--ink-soft);
  }
  .contact__icon { width: 13px; height: 13px; flex: none; }
  .tagline {
    position: absolute; left: 0; right: 0; bottom: 26px; text-align: center;
    font-size: 18px; font-variant: small-caps; letter-spacing: 1px;
  }
  /* Back */
  .card--back {
    display: flex; flex-direction: column; align-items: center; justify-content: center; gap: 28px;
  }
  .back-mark__circle {
    width: 120px; height: 120px; border-radius: 50%;
    background: radial-gradient(circle, #d4d6da 0%, #8a8d93 60%, #3a3b3e 100%);
  }
  .back-mark__name {
    font-size: 24px; letter-spacing: 2px; color: var(--silver); text-transform: uppercase;
  }
</style>
</head>
<body>
<main class="stage">
  <section class="card card--front" aria-label="Business card front">
    <div class="brand-mark">
      <div class="brand-mark__circle" role="img" aria-label="Compass rose emblem in steel blue"></div>
      <span class="brand-mark__name">Quillmere Logistics</span>
    </div>
    <div class="divider"></div>
    <div class="contact">
      <p class="contact__name">Ray Falkner</p>
      <p class="contact__city">Harlow Bay Coast</p>
      <p class="contact__title">President</p>
      <ul class="contact__list">
        <li class="contact__item">
          <svg class="contact__icon" viewBox="0 0 16 16" aria-hidden="true"><path fill="#c9c9cc" d="M3 1h3l1.5 4-2 1.3a9 9 0 0 0 4.2 4.2L11 8.5l4 1.5v3a2 2 0 0 1-2 2A12 12 0 0 1 1 3a2 2 0 0 1 2-2z"/></svg>
          (555) 314-9027
        </li>
        <li class="contact__item">
          <svg class="contact__icon" viewBox="0 0 16 16" aria-hidden="true"><rect x="1" y="3" width="14" height="10" fill="none" stroke="#c9c9cc"/><path d="M1.5 3.5 8 9l6.5-5.5" fill="none" stroke="#c9c9cc"/></svg>
          QuillmereSCL@Examplemail.com
        </li>
      </ul>
    </div>
    <p class="tagline">A Supply Chain and Logistics Consulting Company</p>
  </section>

  <section class="card card--back" aria-label="Business card back">
    <div class="back-mark__circle" role="img" aria-label="Compass rose emblem in silver foil"></div>
    <span class="back-mark__name">Quillmere Logistics</span>
  </section>
</main>
</body>
</html>
```